Corvane Capital Business Cards

These are professional business cards that are for my family office.
Put fake emails and phone numbers as of now until I finalize those components. This family office controls my families investments, assets, and future. The cards should be professional.
..
.
.
.
I just uploaded another variation of a logo I would like to see as a business card to I am inbeteen which logo to use

Target Market(s)

business

Industry/Entity Type

business

Contact Information for Business Card

Professional, wealth related, finance related.

Requirements
Must have
• Logo

```html
<!DOCTYPE html>
<html lang="en">
<head>
<meta charset="utf-8">
<title>Corvane Capital Business Cards</title>
<link rel="stylesheet" href="https://fonts.googleapis.com/css2?family=Montserrat:wght@400;500;700&display=swap">
<style>
  :root {
    --navy: #1b2032;
    --paper: #ffffff;
    --stage: #e9e6e1;
    --grey: #a7a7a7;
  }
  * { margin: 0; padding: 0; box-sizing: border-box; }
  html, body { width: 1200px; height: 931px; overflow: hidden; }
  body {
    position: relative;
    background: var(--stage);
    font-family: "Montserrat", sans-serif;
    color: var(--navy);
  }
  .card {
    position: absolute;
    width: 680px;
    height: 389px;
    background: var(--paper);
    border-radius: 18px;
    overflow: hidden;
    box-shadow: 0 10px 24px rgba(0,0,0,0.18);
  }
  .card::after {
    content: "";
    position: absolute;
    left: 0; right: 0; bottom: 0;
    height: 12px;
    background: var(--navy);
  }
  .card-front { left: 60px; top: 50px; }
  .card-back { left: 460px; top: 490px; }

  .brand {
    position: absolute;
    display: flex;
    align-items: center;
    gap: 16px;
  }
  .brand-dot {
    border: 3px solid var(--navy);
    border-radius: 50%;
  }
  .brand-name {
    font-weight: 500;
    text-transform: uppercase;
    color: var(--navy);
    white-space: nowrap;
  }
  .card-front .brand { left: 50%; top: 50%; transform: translate(-50%, -55%); }
  .card-front .brand-dot { width: 70px; height: 70px; }
  .card-front .brand-name { font-size: 34px; letter-spacing: 5px; }

  .card-back .brand { right: 46px; top: 54px; gap: 12px; }
  .card-back .brand-dot { width: 44px; height: 44px; border-width: 2px; }
  .card-back .brand-name { font-size: 21px; letter-spacing: 3px; }

  .divider {
    position: absolute;
    left: 200px; right: 46px; top: 186px;
    height: 2px;
    background: var(--navy);
  }
  .holder {
    position: absolute;
    left: 46px; top: 152px;
  }
  .holder-name { font-size: 30px; font-weight: 700; line-height: 1.1; }
  .holder-role { font-size: 17px; font-weight: 400; margin-top: 4px; }
  .holder-rule { width: 150px; height: 2px; background: var(--navy); margin-top: 8px; }

  .contact-list {
    position: absolute;
    left: 46px; top: 266px;
    list-style: none;
    font-size: 17px;
  }
  .contact-list li { display: flex; align-items: center; gap: 12px; height: 28px; }
  .contact-list svg { width: 16px; height: 16px; fill: var(--navy); flex: none; }

  .address {
    position: absolute;
    right: 46px; top: 202px;
    text-align: right;
    font-size: 14px;
    line-height: 1.35;
  }
</style>
</head>
<body>
  <section class="card card-front">
    <div class="brand">
      <span class="brand-dot"></span>
      <span class="brand-name">Corvane Capital</span>
    </div>
  </section>

  <section class="card card-back">
    <div class="brand">
      <span class="brand-dot"></span>
      <span class="brand-name">Corvane Capital</span>
    </div>
    <div class="divider"></div>
    <div class="address">42 Harbor Point Plaza<br>Westbrook, NJ 07100 USA</div>
    <div class="holder">
      <div class="holder-name">Marcus Ellery</div>
      <div class="holder-role">Owner</div>
      <div class="holder-rule"></div>
    </div>
    <ul class="contact-list">
      <li>
        <svg viewBox="0 0 24 24" aria-hidden="true"><path d="M6.6 10.8c1.4 2.8 3.8 5.1 6.6 6.6l2.2-2.2c.3-.3.7-.4 1-.2 1.1.4 2.3.6 3.6.6.6 0 1 .4 1 1V20c0 .6-.4 1-1 1C10.6 21 3 13.4 3 4c0-.6.4-1 1-1h3.5c.6 0 1 .4 1 1 0 1.3.2 2.5.6 3.6.1.3 0 .7-.2 1L6.6 10.8z"/></svg>
        (555)214-7788
      </li>
      <li>
        <svg viewBox="0 0 24 24" aria-hidden="true"><path d="M2 5h20v14H2z M2 5l10 8 10-8" /></svg>
        info@corvanecapital.com
      </li>
      <li>
        <svg viewBox="0 0 24 24" aria-hidden="true"><path d="M12 2a10 10 0 1 0 0 20 10 10 0 0 0 0-20zm0 2c1.2 0 2.6 2.5 3 6H9c.4-3.5 1.8-6 3-6zm-3 8h6c-.4 3.5-1.8 6-3 6s-2.6-2.5-3-6zm-4.9-2a8 8 0 0 1 4.6-5.5C8 6 7.3 8 7.1 10H4.1zm0 2h3c.2 2 .9 4 1.6 5.5A8 8 0 0 1 4.1 12zm15.8 0a8 8 0 0 1-4.6 5.5c.7-1.5 1.4-3.5 1.6-5.5h3zm0-2h-3c-.2-2-.9-4-1.6-5.5A8 8 0 0 1 19.9 10z"/></svg>
        www.corvanecapital.com
      </li>
    </ul>
  </section>
</body>
</html>
```